Develop website for Cloud Security Startup

Looking for a logo that conveys the outsourced security and management of clients data, systems and development in Tellix, Bri and Pindle with an emphasis on security and compliance

Target Market(s)

Companies looking for professional services IT firm

Coding

Coded - Design and coding required

Number of Pages Required

5+ page

Font styles to use
Sans Serif

Colors
0455a3
33a6d7

Requirements
Must have
• Landing Page
- Help me get started

Move to the cloud safely
- Benefits of Cloud

What we do
- Cloud Adoption
- Managed Services
- Optimise

Resources
- News
- Resources
- Events
- Webinars
- Not for profit
- Case Studies
- Support Button
- Incident Button

Company
- About Us
- Why Vorplexa?
- Acreditations
- Quorvane Tellix Partner
- Net Promoter Score
- Careers
- Contact Us

Contact Us

```html
<!DOCTYPE html>
<html lang="en">
<head>
<meta charset="utf-8">
<title>Vorplexa — Effective Technology Management</title>
<link href="https://fonts.googleapis.com/css2?family=Lato:wght@400;700;900&family=Montserrat:wght@500;600;700&display=swap" rel="stylesheet">
<style>
:root{
  --brand:#0455a3;
  --brand-light:#33a6d7;
  --ink:#1b1d22;
  --muted:#6b6f78;
  --soft:#f5f5f6;
  --dark:#18181a;
  --white:#ffffff;
}
*{box-sizing:border-box;margin:0;padding:0}
html,body{width:1200px;height:3716px;overflow:hidden}
body{font-family:"Lato",sans-serif;color:var(--ink);background:var(--white);position:relative}
.abs{position:absolute}
a{color:inherit;text-decoration:none}
.btn{position:absolute;display:flex;align-items:center;justify-content:center;border-radius:26px;
  background:linear-gradient(180deg,var(--brand-light) 0%,var(--brand) 100%);color:var(--white);
  font-weight:700;font-size:18px;box-shadow:0 3px 8px rgba(4,85,163,.25)}
.heading{font-family:"Montserrat",sans-serif;font-weight:600;color:var(--ink)}

/* header */
.brand{left:91px;top:30px;display:flex;align-items:center;gap:10px}
.brand-dot{width:40px;height:40px;border-radius:50%;background:var(--brand)}
.brand-name{font-family:"Lato",sans-serif;font-weight:900;font-size:26px;color:var(--brand);letter-spacing:1px}
.topbar{right:88px;top:38px;display:flex;align-items:center;font-size:16px;color:#3a3d44}
.topbar .item{display:flex;align-items:center;gap:8px;padding:0 26px;border-right:1px solid #d6d8dc}
.topbar .item:last-child{border:0;padding-right:0;font-weight:700;color:var(--ink)}
.topbar .login{color:var(--brand);font-weight:700}
.nav{left:0;top:104px;width:1200px;height:46px;background:linear-gradient(180deg,#2e93cf 0%,var(--brand) 100%);
  display:flex;align-items:center;padding-left:123px;gap:56px}
.nav a{color:var(--white);font-weight:700;font-size:16px;text-transform:uppercase}
.nav a.active{color:var(--ink)}

/* hero */
.hero-title{left:91px;top:300px;font-family:"Montserrat",sans-serif;font-weight:700;font-size:64px;color:var(--brand);letter-spacing:1px;z-index:2}
.hero-sub{left:92px;top:376px;font-size:26px;font-weight:400;color:var(--ink);white-space:nowrap;z-index:2}
.art{border-radius:18px}

/* cards */
.section-title{width:1200px;text-align:center;font-size:42px}
.card{position:absolute;top:873px;width:320px;height:238px;border-radius:22px;background:var(--white);
  text-align:center;padding-top:30px}
.card h3{font-weight:700;font-size:21px;margin:16px 0 8px}
.card p{font-size:14px;line-height:29px;color:var(--muted);padding:0 26px}
.card.featured{background:linear-gradient(180deg,var(--brand) 0%,var(--brand-light) 100%);color:var(--white)}
.card.featured p{color:#e6f1fb}

/* benefits */
.benefits{left:91px;top:1400px;width:520px;list-style:none}
.benefits li{position:relative;padding-left:43px;font-size:16px;line-height:29px;color:#3e4148;margin-bottom:13px}
.benefits li::before{content:"";position:absolute;left:2px;top:8px;width:20px;height:20px;border-radius:50%;
  background:var(--brand);box-shadow:inset 0 0 0 5px var(--brand-light)}

/* about */
.about-text{left:588px;top:2108px;width:524px;font-size:16px;line-height:28.6px;color:#55585f;text-align:justify}

/* blog */
.post{position:absolute;top:2657px;width:320px}
.post .thumb{width:320px;height:177px}
.post h4{font-family:"Montserrat",sans-serif;font-weight:500;font-size:23px;line-height:30.5px;margin-top:30px;color:var(--ink)}
.post time{display:block;color:var(--brand-light);font-size:15px;margin-top:6px}
.post p{font-size:14.5px;line-height:28px;color:#4d5057;margin-top:6px}
.post .more{display:block;color:var(--brand);font-weight:700;font-size:17px;margin-top:12px}

/* footer */
.footer-col{color:var(--white)}
.footer-col h5{font-weight:700;font-size:22px;margin-bottom:24px}
.footer-col p,.footer-col li{font-size:14px;line-height:23px}
.links{list-style:none}
.links li{line-height:29.6px}
.email-field{width:305px;height:43px;border-radius:22px;background:var(--white);color:#666;font-size:13px;
  display:flex;align-items:center;padding-left:20px;margin-top:26px}
.contact-row{display:flex;gap:16px;margin-bottom:22px;letter-spacing:.4px}
.contact-ico{flex:0 0 30px;height:30px;border-radius:5px;background:#1b78c9;display:flex;align-items:center;justify-content:center}
.socials{left:0;top:3638px;width:1200px;display:flex;justify-content:center;gap:14px}
.socials span{width:32px;height:32px;border-radius:50%;background:#1b78c9}
.copy{left:0;top:3680px;width:1200px;text-align:center;color:var(--white);font-size:13px}
</style>
</head>
<body>

<!-- header -->
<div class="abs brand"><span class="brand-dot"></span><span class="brand-name">VORPLEXA</span></div>
<div class="abs topbar">
  <div class="item">
    <svg width="16" height="12" viewBox="0 0 16 12"><rect x="0.5" y="0.5" width="15" height="11" rx="1.5" fill="var(--brand)"/><path d="M1 1l7 6 7-6" stroke="#fff" stroke-width="1.4" fill="none"/></svg>
    hello@vorplexa.io
  </div>
  <div class="item login">
    <svg width="13" height="14" viewBox="0 0 13 14"><circle cx="6.5" cy="4" r="3.5" fill="var(--brand)"/><path d="M0 14c0-4 3-6 6.5-6S13 10 13 14z" fill="var(--brand)"/></svg>
    Login
  </div>
  <div class="item">EN <svg width="10" height="6" viewBox="0 0 10 6"><path d="M1 1l4 4 4-4" stroke="#333" stroke-width="1.4" fill="none"/></svg></div>
</div>
<nav class="abs nav">
  <a class="active" href="#">Home</a>
  <a href="#">Move to the cloud safely</a>
  <a href="#">What we do</a>
  <a href="#">Resources</a>
  <a href="#">Company</a>
  <a href="#">Contact us</a>
</nav>

<!-- hero -->
<div class="abs art" role="img" aria-label="Isometric illustration of a team securing cloud servers and a laptop"
  style="left:640px;top:151px;width:500px;height:433px;background:radial-gradient(ellipse at 55% 55%,#cfe6f6 0%,#e9f3fb 55%,#ffffff 80%)"></div>
<h1 class="abs hero-title">VORPLEXA</h1>
<p class="abs hero-sub">EFFECTIVE TECHNOLOGY MANAGEMENT</p>
<a class="btn" href="#" style="left:92px;top:453px;width:211px;height:49px">Get a Free Quote</a>

<!-- what we do band -->
<svg class="abs" style="left:0;top:630px" width="1200" height="630" viewBox="0 0 1200 630">
  <path d="M0 78 C180 40 360 10 560 14 C760 18 900 50 1200 10 L1200 582 C1020 590 880 540 720 562 C560 590 400 520 250 560 C150 585 60 600 0 620 Z" fill="var(--soft)"/>
</svg>
<h2 class="abs heading section-title" style="left:0;top:780px">What we do</h2>

<div class="card" style="left:91px">
  <svg width="66" height="62" viewBox="0 0 66 62" fill="none" stroke="var(--brand)" stroke-width="2">
    <path d="M12 36a10 10 0 0 1 2-20 14 14 0 0 1 27-2 10 10 0 0 1 10 8"/>
    <path d="M20 26v12m-4-4l4 4 4-4"/>
    <rect x="38" y="34" width="20" height="18" rx="2"/><path d="M42 34v-5a6 6 0 0 1 12 0v5"/><circle cx="48" cy="43" r="2"/>
  </svg>
  <h3>Cloud Adoption</h3>
  <p>Lorem ipsum dolor sit amet, consectetur adipiscing elit, sed do eiusmod tempor incididunt ut labore et dolorequa.</p>
</div>
<div class="card featured" style="left:440px">
  <svg width="66" height="62" viewBox="0 0 66 62" fill="none" stroke="#fff" stroke-width="2">
    <circle cx="33" cy="24" r="9"/>
    <path d="M33 6v6M33 36v6M15 24h6M45 24h6M20 11l4 4M42 33l4 4M46 11l-4 4M24 33l-4 4"/>
    <path d="M10 58v-8a8 8 0 0 1 8-8h8l8 6h10"/><path d="M4 46h8v14H4z"/>
  </svg>
  <h3>Managed Services</h3>
  <p>Lorem ipsum dolor sit amet, consectetur adipiscing elit, sed do eiusmod tempor</p>
</div>
<div class="card" style="left:790px">
  <svg width="66" height="62" viewBox="0 0 66 62" fill="none" stroke="var(--brand)" stroke-width="2">
    <rect x="8" y="4" width="50" height="52" rx="2"/><path d="M8 12h50M14 20h20M14 27h16M14 34h14M14 41h18M14 48h12"/>
    <circle cx="44" cy="36" r="8"/><path d="M50 42l6 6"/>
  </svg>
  <h3>Optimise</h3>
  <p>Lorem ipsum dolor sit amet, consectetur adipiscing elit, sed do mod tempor incididunt ut labore et</p>
</div>

<!-- benefits -->
<h2 class="abs heading" style="left:91px;top:1318px;font-size:42px">Benefits of Cloud</h2>
<ul class="abs benefits">
  <li>Lorem ipsum dolor sit amet, consectetur adipiscing elit, sed do eiusmod tempor incididunt ut labore etb aliqua.</li>
  <li>Lorem ipsum dolor sit amet, consectetur adipiscing elit, sed do eiusmod tempor incididunt ut labore etb aliqua.</li>
  <li>Lorem ipsum dolor sit amet, consectetur adipiscing elit, sed do eiusmod tempor incididunt ut labore etb aliqua.</li>
  <li>Lorem ipsum dolor sit amet, consectetur adipiscing elit, sed do eiusmod tempor incididunt ut labore etb aliqua.</li>
  <li>Lorem ipsum dolor sit amet, consectetur adipiscing elit, sed do eiusmod tempor incididunt ut labore etb aliqua.</li>
</ul>
<a class="btn" href="#" style="left:94px;top:1758px;width:209px;height:48px">Read More</a>
<div class="abs art" role="img" aria-label="Illustration of a person working on a laptop beside a large secure cloud server rack"
  style="left:689px;top:1324px;width:414px;height:482px;background:radial-gradient(ellipse at 60% 50%,#5b6fc4 0%,#8fa0de 40%,#e3e9f8 70%,#ffffff 85%)"></div>

<!-- about band -->
<svg class="abs" style="left:0;top:1900px" width="1200" height="610" viewBox="0 0 1200 610">
  <path d="M0 50 C160 30 300 0 460 10 C620 22 760 50 900 30 C1020 14 1120 20 1200 40 L1200 540 C1040 560 900 520 760 540 C620 560 480 520 320 540 C200 556 90 590 0 600 Z" fill="var(--soft)"/>
</svg>
<div class="abs art" role="img" aria-label="Illustration of a server rack, clouds, gears and a monitor showing code"
  style="left:50px;top:2062px;width:498px;height:267px;background:linear-gradient(90deg,#bfe0f6 0%,#e4edf5 45%,#f5f5f6 100%)"></div>
<h2 class="abs heading" style="left:588px;top:2030px;font-size:42px">About Us</h2>
<p class="abs about-text">Lorem ipsum dolor sit amet, consectetur adipiscing elit, sed do eiusmod tempor incididunt ut labore et dolore magna aliqua. Ut enim ad minim veniam, quis nostrud exercitation ullamco laboris nisi ut aliquip ex ea commodo consequat. Duis aute irure dolor in reprehenderit in voluptate velit esse cillum dolore eu fugiat nulla pariatur. Excepteur sint occaecat cupidatat non proident</p>
<a class="btn" href="#" style="left:588px;top:2315px;width:210px;height:48px">Read More</a>

<!-- blog -->
<h2 class="abs heading section-title" style="left:0;top:2582px">Latest Blog</h2>
<article class="post" style="left:91px">
  <div class="thumb" role="img" aria-label="Photo of colleagues discussing work at a desk with computers" style="background:linear-gradient(135deg,#9aa4ad 0%,#d7d9d7 50%,#6f6a62 100%)"></div>
  <h4>Lorem ipsum dolor sit tur adipiscing elit, sed do mod tempor inca aliqua.</h4>
  <time>Sep 24, 2020</time>
  <p>Lorem ipsum dolor sit amet, consectetur adipiscing elit, sed do eiusmod tempor incididunt ut labore et dolore magna aliqua.</p>
  <a class="more" href="#">Read More</a>
</article>
<article class="post" style="left:440px">
  <div class="thumb" role="img" aria-label="Photo of hands on a laptop with glowing digital network graphics" style="background:linear-gradient(135deg,#1f3a4c 0%,#4f7e93 50%,#17262f 100%)"></div>
  <h4>Lorem ipsum dolor sit tur adipiscing elit, sed do mod tempor inca aliqua.</h4>
  <time>Sep 24, 2020</time>
  <p>Lorem ipsum dolor sit amet, consectetur adipiscing elit, sed do eiusmod tempor incididunt ut labore et dolore magna aliqua.</p>
  <a class="more" href="#">Read More</a>
</article>
<article class="post" style="left:789px">
  <div class="thumb" role="img" aria-label="Photo of a man planning on a whiteboard covered with sticky notes" style="background:linear-gradient(135deg,#c9dbe6 0%,#eef0ee 50%,#5a6a78 100%)"></div>
  <h4>Lorem ipsum dolor sit tur adipiscing elit, sed do mod tempor inca aliqua.</h4>
  <time>Sep 24, 2020</time>
  <p>Lorem ipsum dolor sit amet, consectetur adipiscing elit, sed do eiusmod tempor incididunt ut labore et dolore magna aliqua.</p>
  <a class="more" href="#">Read More</a>
</article>

<!-- footer -->
<svg class="abs" style="left:0;top:3160px" width="1200" height="556" viewBox="0 0 1200 556">
  <path d="M0 70 C120 100 240 120 380 100 C540 78 620 20 760 30 C900 40 980 90 1100 50 C1140 36 1175 20 1200 10 L1200 556 L0 556 Z" fill="var(--dark)"/>
</svg>
<div class="abs footer-col" style="left:128px;top:3320px;width:320px">
  <h5>Sign up for newsletter</h5>
  <p>Excepteur sint occaecat cupidatat non proident, sunt in culpa qui officia deserunt</p>
  <div class="email-field">Enter email</div>
  <a class="btn" href="#" style="position:relative;margin-top:26px;width:129px;height:39px;font-size:16px">Sign up</a>
</div>
<div class="abs footer-col" style="left:542px;top:3320px">
  <h5>Quick Links</h5>
  <ul class="links">
    <li>Home</li><li>Move to the cloud safely</li><li>What we do</li><li>Resources</li><li>Company</li><li>Contact Us</li>
  </ul>
</div>
<div class="abs footer-col" style="left:815px;top:3318px;width:250px">
  <h5>Contact Us</h5>
  <div class="contact-row">
    <span class="contact-ico"><svg width="14" height="18" viewBox="0 0 14 18"><path d="M7 1a6 6 0 0 0-6 6c0 4.5 6 10 6 10s6-5.5 6-10a6 6 0 0 0-6-6z" fill="none" stroke="#fff" stroke-width="1.6"/><circle cx="7" cy="7" r="2" fill="#fff"/></svg></span>
    <p>212 Harlow Creek Road Denbury, New South Wales 2781</p>
  </div>
  <div class="contact-row">
    <span class="contact-ico"><svg width="16" height="16" viewBox="0 0 16 16"><path d="M3 1l3 3-2 2c1 2 3 4 6 6l2-2 3 3-2 2C7 15 1 9 1 3z" fill="none" stroke="#fff" stroke-width="1.4"/></svg></span>
    <p>Call us today:<br>07 41 28 63 90</p>
  </div>
  <div class="contact-row">
    <span class="contact-ico"><svg width="16" height="12" viewBox="0 0 16 12"><rect x="0.7" y="0.7" width="14.6" height="10.6" fill="none" stroke="#fff" stroke-width="1.4"/><path d="M1 1l7 6 7-6" stroke="#fff" stroke-width="1.4" fill="none"/></svg></span>
    <p>Email :<br>hello@vorplexa.io</p>
  </div>
</div>
<div class="abs socials" aria-label="Social links"><span></span><span></span><span></span><span></span><span></span></div>
<p class="abs copy">© Copyright 2021 The Company name. All Rights Reserved.</p>

</body>
</html>
```